Website for IT consulting Company

I need a website upgrade, the existing site content is ok, I would also like to add a testimonial page, the site should be something that is easy for us to update content. You use the content from www.kelvanbrook.com as an example. I will also post update logo and artwork. I also need a contact form with some type of validation or captcha.

I added Coded to the Project

Please omit Address maps

Target Market(s)

small business, service oriented companies. We provide IT Consulting, support and mangement

Industry/Entity Type

Information Technology

Coding

Number of Pages Required

1 page

Font styles to use
Serif
Sans Serif

Requirements
Must have
• Contain logo attached, and content from existing web site www.kelvanbrook.com.
• Also need to update content easily, and be movable to different platforms.
• There is a catch phrase
• "Let us worry about your technology…” “ so you don’t have to!”
• Should be included.
Nice to have
• Testimonial page, Project page where we can post new and past projects and pictures
Should not have
• none

```html
<!DOCTYPE html>
<html lang="en">
<head>
<meta charset="utf-8">
<title>Kelvanbrook Tech Group, Inc.</title>
<link rel="stylesheet" href="https://fonts.googleapis.com/css2?family=Roboto+Slab:wght@400;700&family=Roboto+Condensed:wght@400;700&family=Arimo:ital,wght@0,400;0,700;1,400&display=swap">
<style>
:root{
  --blue:#1b8bd3;
  --blue-dark:#0f6fb5;
  --blue-light:#3aa6e8;
  --ink:#1e1e1e;
  --text:#333;
  --muted:#777;
  --grey-band:#e7e7e7;
  --white:#fff;
  --footer-text:#d8d8d8;
}
*{margin:0;padding:0;box-sizing:border-box}
html,body{width:1200px;height:2436px;overflow:hidden;background:var(--white)}
body{position:relative;font-family:"Arimo",Arial,sans-serif;color:var(--text)}
.abs{position:absolute}

/* header */
.site-header{position:absolute;left:0;top:0;width:1200px;height:108px}
.brand{left:82px;top:34px;display:flex;align-items:center;gap:12px}
.brand-mark{width:34px;height:34px;background:var(--blue)}
.brand-name{font-family:"Roboto Slab",serif;font-weight:700;font-size:30px;color:var(--ink);line-height:1}
.follow{right:52px;top:10px;display:flex;align-items:center;gap:8px;font-family:"Roboto Slab",serif;font-size:15px;color:var(--ink)}
.follow .dot{width:38px;height:38px;border-radius:50%;background:#9a9a9a;border:3px solid #ddd}
.follow .dot.on{background:var(--blue)}
.contact-line{right:52px;top:64px;display:flex;align-items:center;gap:10px;font-family:"Roboto Slab",serif;font-size:19px;color:#555}
.contact-line .phone{font-size:21px;color:var(--ink)}

/* nav */
.main-nav{position:absolute;left:0;top:107px;width:1200px;height:45px;background:linear-gradient(#2a9be0,var(--blue-dark));display:flex;justify-content:space-between;padding:0 95px 0 96px;align-items:center}
.main-nav a{font-family:"Roboto Slab",serif;font-size:16px;color:var(--white);text-decoration:none;letter-spacing:.3px}
.main-nav a.active{color:var(--ink)}

/* hero */
.hero{position:absolute;left:0;top:152px;width:1200px;height:533px;background:linear-gradient(100deg,#c8d3dc 0%,#e9eef2 35%,#b9c4cf 62%,#3d4f66 100%)}
.hero-caption{position:absolute;left:0;bottom:0;width:100%;height:56px;background:rgba(30,30,30,.72);text-align:center;font-family:"Roboto Condensed",sans-serif;font-size:35px;line-height:56px;color:var(--white)}
.hero-caption span{color:var(--blue-light)}

/* section titles */
.section-title{position:absolute;left:0;width:1200px;text-align:center;font-family:"Roboto Slab",serif;font-weight:700;font-size:28px;color:var(--ink)}
.section-title span{color:var(--blue)}
.title-rule{position:absolute;left:560px;width:80px;height:2px;background:#9a9a9a}

/* services */
.service-card{position:absolute;top:833px;width:315px;height:186px;background:var(--white);border-radius:10px;box-shadow:0 5px 10px rgba(0,0,0,.18);border:1px solid #eee;text-align:center}
.service-icon{position:absolute;left:121px;top:-33px;width:72px;height:72px;border-radius:4px;display:flex;align-items:center;justify-content:center}
.service-icon.blue{background:var(--blue)}
.service-icon.grey{background:linear-gradient(#9a9a9a,#6e6e6e)}
.service-card h3{margin-top:64px;font-family:"Roboto Condensed",sans-serif;font-weight:400;font-size:19px;color:#444}
.service-card p{margin:10px auto 0;width:240px;font-size:13px;line-height:20px;color:#555}
.service-more{position:absolute;left:143px;bottom:-1px;width:28px;height:20px;color:var(--white);font-size:18px;line-height:20px;font-weight:700}
.service-more.blue{background:var(--blue)}
.service-more.grey{background:#8c8c8c}

/* welcome */
.welcome{position:absolute;left:0;top:1073px;width:1200px;height:285px;background:var(--grey-band)}
.welcome-text{position:absolute;left:90px;top:115px;width:1020px;text-align:center;font-size:13.5px;line-height:26px;color:#222}
.read-more{font-family:"Roboto Slab",serif;font-size:16px;color:var(--ink);text-decoration:underline;text-underline-offset:4px}

/* feature columns */
.feature-col{position:absolute;top:1358px;width:540px;height:368px}
.feature-col h2{position:absolute;left:42px;top:56px;font-family:"Roboto Slab",serif;font-weight:700;font-size:23px;color:var(--ink);white-space:nowrap}
.feature-col h2 span{color:var(--blue)}
.feature-col .icon{position:absolute;left:0;top:52px}
.feature-col .rule{position:absolute;left:0;top:96px;width:80px;height:2px;background:#9a9a9a}
.feature-photo{position:absolute;left:0;top:129px;width:203px;height:184px;border:3px solid #555}
.feature-text{position:absolute;left:226px;top:126px;width:255px;font-size:13.5px;line-height:26px;color:#222}
.feature-text .read-more{display:inline-block;margin-top:6px;font-size:15px}
.col-divider{position:absolute;left:601px;top:1410px;width:1px;height:270px;background:#e2e2e2}

/* testimonials */
.testimonials{position:absolute;left:0;top:1726px;width:1200px;height:269px;background:var(--grey-band);z-index:3}
.quote{position:absolute;left:225px;top:140px;width:750px;text-align:center;font-style:italic;font-size:15px;line-height:29px;color:#222}
.quote-mark{position:absolute;font-family:"Roboto Slab",serif;font-size:40px;color:#aaa}
.client-name{position:absolute;left:0;top:250px;width:1200px;text-align:center;font-weight:700;font-size:17px;color:#222}
.client-place{position:absolute;left:0;top:276px;width:1200px;text-align:center;font-weight:700;font-size:14px;color:#222}

/* footer */
.site-footer{position:absolute;left:0;top:2010px;width:1200px;height:380px;background:linear-gradient(180deg,#30343b 0%,#1d1f24 60%,#2b2520 100%)}
.footer-wave{position:absolute;left:0;top:1995px}
.footer-col{position:absolute;top:2118px}
.footer-col h4{font-family:"Arimo",sans-serif;font-weight:400;font-size:18px;color:var(--white)}
.footer-col h4 span{color:var(--blue-light)}
.footer-col .under{width:130px;height:1px;background:#555;margin-top:8px}
.quick-links{list-style:none;margin-top:14px}
.quick-links li{font-size:13.5px;color:var(--footer-text);line-height:25px;padding-left:14px;position:relative}
.quick-links li::before{content:"";position:absolute;left:0;top:11px;width:4px;height:4px;border-radius:50%;background:#e0a030}
.address{margin-top:14px;font-size:14px;line-height:23px;color:var(--footer-text)}
.contact-row{display:flex;align-items:center;gap:12px;font-size:13.5px;color:var(--footer-text);margin-top:14px}
.social-row{display:flex;align-items:center;gap:24px;font-size:13.5px;color:var(--footer-text);margin-top:14px}
.social-row .dot{width:30px;height:30px;border-radius:50%;background:#8e8e8e;border:2px solid #ccc}
.social-row .dot.on{background:var(--blue)}
.footer-sep{position:absolute;top:2116px;width:1px;height:230px;background:#44474d}
.copyright{position:absolute;left:0;top:2390px;width:1200px;height:46px;background:linear-gradient(#2a9be0,var(--blue-dark));text-align:center;line-height:46px;font-size:14px;color:var(--white)}
</style>
</head>
<body>

<header class="site-header">
  <div class="abs brand"><div class="brand-mark"></div><div class="brand-name">KELVANBROOK</div></div>
  <div class="abs follow">Follow Us On
    <span class="dot on"></span><span class="dot"></span><span class="dot"></span><span class="dot"></span>
  </div>
  <div class="abs contact-line">
    <svg width="22" height="14" viewBox="0 0 22 14"><rect x="1" y="1" width="20" height="12" fill="none" stroke="#1b8bd3" stroke-width="2"/><path d="M1 1l10 7 10-7" fill="none" stroke="#1b8bd3" stroke-width="2"/></svg>
    <span>inquiry@kelvanbrook.com</span>
    <svg width="22" height="22" viewBox="0 0 22 22" style="margin-left:14px"><circle cx="11" cy="11" r="10" fill="none" stroke="#1b8bd3" stroke-width="1.5"/><path d="M7 6c1-1 2 0 3 2s-1 2 0 3 1 2 3 2 2 1 1 2-4 1-6-2-2-6-1-7z" fill="#1b8bd3"/></svg>
    <span class="phone">(555) 014-2270</span>
  </div>
</header>

<nav class="main-nav">
  <a class="active" href="#">HOME</a><a href="#">ABOUT US</a><a href="#">SERVICES</a><a href="#">SUPPORT</a><a href="#">CLIENTS</a><a href="#">CAREERS</a><a href="#">CONTACT US</a>
</nav>

<section class="hero" role="img" aria-label="Photo of a business team smiling in a meeting around a table">
  <div class="hero-caption">Let Us Worry About Your Technology... <span>So You Don't Have To!</span></div>
</section>

<h2 class="section-title" style="top:728px">OUR <span>SERVICES</span></h2>

<article class="service-card" style="left:81px">
  <div class="service-icon blue"><svg width="46" height="46" viewBox="0 0 46 46" fill="none" stroke="#fff" stroke-width="2.5"><circle cx="23" cy="23" r="5"/><path d="M23 3v15M23 28v15M3 23h15M28 23h15M9 9l10 10M27 27l10 10M37 9L27 19M19 27L9 37"/></svg></div>
  <h3>Managed IT Solutions</h3>
  <p>Duis autem vel eum iriure do in hendrerit in vulputate Duis autem he....</p>
  <div class="service-more blue">+</div>
</article>
<article class="service-card" style="left:445px">
  <div class="service-icon grey"><svg width="46" height="46" viewBox="0 0 46 46" fill="none" stroke="#fff" stroke-width="3"><circle cx="23" cy="19" r="9"/><path d="M9 42c0-9 6-13 14-13s14 4 14 13M12 19a11 11 0 0 1 22 0"/></svg></div>
  <h3>Remote Diagnostic &amp; Support</h3>
  <p>Duis autem vel eum iriure do in hendrerit in vulputate Duis autem he....</p>
  <div class="service-more grey">+</div>
</article>
<article class="service-card" style="left:809px">
  <div class="service-icon grey"><svg width="48" height="46" viewBox="0 0 48 46" fill="#fff"><rect x="4" y="18" width="18" height="18"/><rect x="26" y="18" width="18" height="18"/><rect x="10" y="8" width="8" height="10"/><rect x="30" y="8" width="8" height="10"/></svg></div>
  <h3>Infrastructure Design &amp; Installation</h3>
  <p>Duis autem vel eum iriure do in hendrerit in vulputate Duis autem he....</p>
  <div class="service-more grey">+</div>
</article>

<section class="welcome">
  <h2 class="section-title" style="top:45px">WELCOME TO <span>KELVANBROOK TECH GROUP, INC</span></h2>
  <div class="title-rule" style="top:90px"></div>
  <p class="welcome-text">Kelvanbrook Tech Group, Inc. was established in 1991. Our mission is helping businesses and individuals realize a Return on Investment by implementing today's advanced technologies. As a small business we understand the importance of technology and personalized attention. Every member of our support team has worked with both large and small companies supporting a multitude of applications, networks and environments.</p>
  <a class="read-more abs" href="#" style="left:554px;top:216px">Read More</a>
</section>

<section class="feature-col" style="left:83px">
  <svg class="icon" width="30" height="36" viewBox="0 0 30 36" fill="#1b8bd3"><circle cx="15" cy="9" r="7"/><path d="M2 34c0-9 6-13 13-13s13 4 13 13z"/></svg>
  <h2>IT SUPPORT <span>SOLUTIONS</span></h2>
  <div class="rule"></div>
  <div class="feature-photo" role="img" aria-label="Photo of two technicians checking a server rack" style="background:linear-gradient(135deg,#4a5f7a,#9fb2c6 55%,#2f3b4c)"></div>
  <p class="feature-text">Lorem ipsum dolor sit amet, consecretk etuer adipiscing elit, sed diam nonumre my nibh euismod tinciduntol ut laoret et re olore magna aliquam erat volutpt. Ut wisi minim consequat. Lorem ipsum dolor sit amet, consecretk...<br><a class="read-more" href="#">Read More</a></p>
</section>
<div class="col-divider"></div>
<section class="feature-col" style="left:633px">
  <svg class="icon" width="36" height="36" viewBox="0 0 36 36" fill="#1b8bd3"><circle cx="18" cy="6" r="4"/><circle cx="6" cy="12" r="3.5"/><circle cx="30" cy="12" r="3.5"/><rect x="14" y="12" width="8" height="12"/><rect x="3" y="17" width="6" height="10"/><rect x="27" y="17" width="6" height="10"/><rect x="2" y="30" width="32" height="3"/></svg>
  <h2>OUR OUTSCOURCING <span>TECHNOLOGY</span></h2>
  <div class="rule"></div>
  <div class="feature-photo" role="img" aria-label="Illustration of a glowing globe above a hand holding a tablet" style="background:radial-gradient(circle at 50% 40%,#6fb7ef,#1b3f6e 55%,#0b1628)"></div>
  <p class="feature-text">Lorem ipsum dolor sit amet, consecretk etuer adipiscing elit, sed diam nonumre my nibh euismod tinciduntol ut laoret et re olore magna aliquam erat volutpt. Ut wisi minim consequat. Lorem ipsum dolor sit amet, consecretk...<br><a class="read-more" href="#">Read More</a></p>
</section>

<footer class="site-footer" role="img" aria-label="Night city skyline photo behind the footer"></footer>
<svg class="footer-wave" width="1200" height="110" viewBox="0 0 1200 110">
  <path d="M0 0H1200V40C950 60 800 110 560 105 300 98 120 60 0 15Z" fill="#e7e7e7"/>
  <path d="M0 15C120 60 300 98 560 105" fill="none" stroke="#a9abae" stroke-width="10"/>
  <path d="M520 106C800 100 980 40 1200 28V50C990 56 820 104 560 112Z" fill="#1b8bd3"/>
</svg>

<section class="testimonials">
  <h2 class="section-title" style="top:44px">CLIENTS <span>TESTIMONIALS</span></h2>
  <div class="title-rule" style="top:88px"></div>
  <span class="quote-mark" style="left:207px;top:120px">&ldquo;</span>
  <p class="quote">Lorem ipsum dolor sit amet, consectetuer adipiscing elit, sed diam nonummy nibh euismod tinciduntut laoreet dolore magna aliquam erat volutpat. Ut wisi enim ad minim veniam, quis nostrud exercimori mornkle tation ullamcorper suscipit lobortis nisl ut aliquip ex ea commodo consequat.</p>
  <span class="quote-mark" style="left:880px;top:188px">&rdquo;</span>
  <svg class="abs" style="left:115px;top:190px" width="30" height="56" viewBox="0 0 30 56"><path d="M28 2L2 28l26 26" fill="none" stroke="#999" stroke-width="1.5"/></svg>
  <svg class="abs" style="left:1057px;top:190px" width="30" height="56" viewBox="0 0 30 56"><path d="M2 2l26 26L2 54" fill="none" stroke="#999" stroke-width="1.5"/></svg>
  <div class="client-name">Renata L.</div>
  <div class="client-place">Harbor Point, CA</div>
</section>

<div class="footer-col" style="left:88px">
  <h4>Quick <span>Links</span></h4><div class="under"></div>
  <ul class="quick-links"><li>Home</li><li>About Us</li><li>Services</li><li>Support</li><li>Clients</li><li>Careers</li><li>Contact Us</li></ul>
</div>
<div class="footer-sep" style="left:268px"></div>
<div class="footer-col" style="left:320px">
  <h4>Contact <span>Details</span></h4><div class="under"></div>
  <p class="address" style="font-size:14.5px">Kelvanbrook Tech Group, Inc.</p>
  <p class="address" style="margin-top:6px;font-size:13px;line-height:21px">418 Marlow Ave.<br>Springdale, Texas 75001</p>
  <div class="contact-row" style="margin-top:24px"><svg width="14" height="14" viewBox="0 0 14 14"><path d="M2 1c2-1 3 1 4 3s-1 2 0 3 2 2 3 1 2 0 3 2-3 4-7 0-5-8-3-9z" fill="#3aa6e8"/></svg>(555) 014-2270</div>
  <div class="contact-row"><svg width="14" height="14" viewBox="0 0 14 14" fill="#3aa6e8"><rect x="3" y="1" width="8" height="4"/><rect x="1" y="5" width="12" height="6"/><rect x="3" y="9" width="8" height="4" fill="#fff"/></svg>(555) 014-2270</div>
  <div class="contact-row"><svg width="14" height="10" viewBox="0 0 14 10"><rect width="14" height="10" fill="#3aa6e8"/><path d="M0 0l7 5 7-5" fill="none" stroke="#fff"/></svg>inquiry@kelvanbrook.com</div>
</div>
<div class="footer-sep" style="left:622px"></div>
<div class="footer-col" style="left:643px">
  <h4>Get <span>Social</span></h4><div class="under"></div>
  <div class="social-row"><span class="dot on"></span>Circlebook</div>
  <div class="social-row"><span class="dot"></span>Tweetline</div>
  <div class="social-row"><span class="dot"></span>PlusCircle</div>
  <div class="social-row"><span class="dot"></span>Linkwork</div>
</div>

<div class="copyright">Copyright &copy; 2017 Kelvanbrook Tech Group, Inc. All Rights Reserved.</div>

</body>
</html>
```